Timber Crest Construction Needs business card

Hey we are in need of business card designs. I have upload our logo as a guideline, but free feel to run with it or come up with something unique.
Pls have fun with it and be creative. the name says it all!
i will give some directions after i see a few entries..
Updates
Logo source file has been uploaded..
Hey because of the logo is so colourful already.
Can we have a few submissions with less colour.
Also we are looking for clever/hidden/descriptive business card.

```html
<!DOCTYPE html>
<html lang="en">
<head>
<meta charset="utf-8">
<title>Timber Crest Construction — Business Card</title>
<link rel="stylesheet" href="https://fonts.googleapis.com/css2?family=PT+Sans:wght@400;700&display=swap">
<style>
  :root {
    --backdrop: #e9e6e2;
    --card-white: #ffffff;
    --card-black: #0d0d0d;
    --brand-grey: #5f6468;
    --brand-grey-dark: #55595c;
    --text-white: #ffffff;
    --text-soft: #e6e6e6;
    --rule: #9a9a9a;
    --band: #2a2a2a;
    --accent-square: #5f6468;
  }
  * { box-sizing: border-box; margin: 0; padding: 0; }
  html, body {
    width: 1200px; height: 470px; overflow: hidden;
    background: var(--backdrop);
    font-family: "PT Sans", sans-serif;
  }
  .canvas {
    position: relative; width: 1200px; height: 470px;
  }
  .card {
    position: absolute; top: 70px; width: 520px; height: 320px;
    box-shadow: 0 6px 18px rgba(0,0,0,0.25);
  }
  .card--front { left: 50px; background: var(--card-white); }
  .card--back { left: 630px; background: var(--card-black); overflow: hidden; }

  /* front */
  .front-brand {
    position: absolute; left: 0; right: 0; top: 112px;
    display: flex; align-items: center; justify-content: center; gap: 16px;
  }
  .brand-square {
    width: 62px; height: 62px; background: var(--accent-square);
  }
  .brand-name {
    color: var(--brand-grey);
    font-weight: 700; line-height: 1.02; text-transform: uppercase;
  }
  .front-brand .brand-name { font-size: 36px; }
  .front-brand .brand-name small { display: block; font-size: 36px; }

  /* back */
  .back-brand {
    position: absolute; left: 70px; top: 62px;
    font-size: 40px; color: var(--brand-grey-dark);
  }
  .holder {
    position: absolute; left: 206px; top: 158px;
    color: var(--text-white); font-weight: 700; font-size: 21px;
  }
  .address {
    position: absolute; left: 116px; top: 226px; width: 160px;
    text-align: right; color: var(--text-soft); font-size: 14px; line-height: 1.35;
  }
  .divider {
    position: absolute; left: 290px; top: 196px; width: 1px; height: 80px;
    background: var(--rule);
  }
  .contacts {
    position: absolute; left: 302px; top: 192px; list-style: none;
    color: var(--text-soft); font-size: 13.5px;
  }
  .contacts li { display: flex; align-items: center; gap: 6px; height: 21px; }
  .contacts svg { width: 12px; height: 12px; flex: none; }
  .base-band {
    position: absolute; left: 80px; right: 20px; height: 2px; background: var(--band);
  }
  .base-band--one { top: 296px; }
  .base-band--two { top: 302px; }
</style>
</head>
<body>
<main class="canvas">
  <section class="card card--front" aria-label="Card front">
    <div class="front-brand">
      <span class="brand-square"></span>
      <p class="brand-name">Timber Crest<small>Construction</small></p>
    </div>
  </section>

  <section class="card card--back" aria-label="Card back">
    <p class="brand-name back-brand">Timber Crest<br>Construction</p>
    <p class="holder">Your Name, Title</p>
    <p class="address">Street Name City Name<br>State Zipcode</p>
    <span class="divider"></span>
    <ul class="contacts">
      <li>
        <svg viewBox="0 0 12 12" aria-hidden="true"><circle cx="6" cy="6" r="5.5" fill="#e6e6e6"/><path d="M4 3.2l1.1 1.3-.6.8c.4.9 1 1.5 1.9 1.9l.8-.6 1.3 1.1-.6 1c-2.4-.3-4.3-2.2-4.6-4.6z" fill="#0d0d0d"/></svg>
        0412 555 018
      </li>
      <li>
        <svg viewBox="0 0 12 12" aria-hidden="true"><circle cx="6" cy="6" r="5.5" fill="#e6e6e6"/><path d="M4 3.2l1.1 1.3-.6.8c.4.9 1 1.5 1.9 1.9l.8-.6 1.3 1.1-.6 1c-2.4-.3-4.3-2.2-4.6-4.6z" fill="#0d0d0d"/></svg>
        0412 555 018
      </li>
      <li>
        <svg viewBox="0 0 12 12" aria-hidden="true"><rect x="0.5" y="2.5" width="11" height="7.5" rx="1" fill="#e6e6e6"/><path d="M1 3l5 4 5-4" fill="none" stroke="#0d0d0d" stroke-width="1"/></svg>
        hello@timbercrestbuild.com
      </li>
      <li>
        <svg viewBox="0 0 12 12" aria-hidden="true"><circle cx="6" cy="6" r="5" fill="none" stroke="#e6e6e6" stroke-width="1.1"/><ellipse cx="6" cy="6" rx="2.2" ry="5" fill="none" stroke="#e6e6e6" stroke-width="0.9"/><path d="M1 6h10" stroke="#e6e6e6" stroke-width="0.9"/></svg>
        www.timbercrestbuild.com
      </li>
    </ul>
    <span class="base-band base-band--one"></span>
    <span class="base-band base-band--two"></span>
  </section>
</main>
</body>
</html>
```